Upstart Retirement Planning Firm needs help with business card design

Harborview Nest Advisors, LLC is looking for help with business card design. We give advice on investments, insurance, and other financial matters related to retirement. There are some required disclosures that we will provide but mostly we are looking for a professional, classy business card that reflects the theme we have chosen. We have a logo that is attached but we would like to add a phrase; "Turning Your Earned Income Into Retirement Income"

Doubled sided only so that we can add the required disclosures (needed for our industry) on the back of the card. We will provide the exact words for this in 1-2 days.

Target Market(s)

Retirees and Pre-retirees. Professionals 50+ years old

Industry/Entity Type

Financial Planning

Contact Information for Business Card

We currently have two people who will need separate cards so we'd like to have a template so that we can add names for new cards in the future.

For the first run, please show the following information.

Gregor Pelham, MBA, ChFC®, CLU®
Financial Advisor, Registered Representative
gpelham@harborviewnest.example
Phone: (555) 318-2946
Toll Free Fax: (800) 555-0193

Address is
2187 Meadowlark Ridge Rd.
Suite K418
Virginia Beach, VA 23999

Colors
3277b5

Requirements
Must have
• Logo, contact info, small phase to describe business (in description), required legal disclosures on back of the card as follows (in small font)
• Gregor Pelham is a registered representative of and offers securities through Brightmoor Capital Brokerage Corporation, Member FNQX. Brightmoor Capital Brokerage Corporation is a member of the Brightmoor Capital Alliance which is the marketing name for Brightmoor Holding Corporation and its affiliates.
Nice to have
• Rounded edges, raised letters
Should not have
• any colors that aren't in the logo (other than black for font)

```html
<!DOCTYPE html>
<html lang="en">
<head>
<meta charset="utf-8">
<title>Harborview Nest Advisors, LLC — Business Card</title>
<link rel="stylesheet" href="https://fonts.googleapis.com/css2?family=Tinos:ital,wght@0,400;0,700;1,400&display=swap">
<style>
  :root {
    --page-bg: #d9d6d2;
    --card-black: #161616;
    --card-black-soft: #1f1f1f;
    --brand-blue: #3277b5;
    --band-blue: #1f5fa8;
    --silver: #b9bcc0;
    --silver-dim: #6e7176;
    --text-light: #e6e6e6;
    --text-muted: #9a9da1;
  }
  * { box-sizing: border-box; margin: 0; padding: 0; }
  html, body {
    width: 1200px; height: 716px; overflow: hidden;
    background: var(--page-bg);
    font-family: "Tinos", "Times New Roman", serif;
  }
  .canvas {
    position: relative; width: 1200px; height: 716px;
    display: flex; align-items: center; justify-content: center; gap: 50px;
  }
  .card {
    position: relative; width: 530px; height: 303px;
    border-radius: 10px; overflow: hidden;
    background: linear-gradient(160deg, var(--card-black-soft), var(--card-black));
    box-shadow: 0 10px 24px rgba(0,0,0,.28);
  }

  /* Back side */
  .card--back { display: flex; align-items: center; justify-content: center; }
  .brand-mark {
    display: flex; align-items: center; gap: 12px;
    margin-top: -30px;
    color: var(--silver-dim);
    font-size: 24px; letter-spacing: 2px; text-transform: uppercase;
  }
  .brand-mark__dot {
    width: 14px; height: 14px; border-radius: 50%;
    background: var(--silver-dim); flex: none;
  }
  .disclosure {
    position: absolute; left: 34px; right: 34px; bottom: 22px;
    color: var(--text-muted); font-size: 8.5px; line-height: 1.4;
    text-align: center;
  }

  /* Front side */
  .card__band {
    position: absolute; left: 0; top: 0; bottom: 0; width: 38px;
    background: var(--band-blue);
    border-right: 6px solid var(--silver);
  }
  .person {
    position: absolute; left: 68px; top: 30px;
  }
  .person__name { color: var(--brand-blue); font-size: 22px; }
  .person__creds, .person__role {
    color: var(--text-light); font-size: 11.5px; line-height: 1.35;
  }
  .person__creds { margin-top: 6px; }
  .person__role { font-style: italic; }

  .brand-front {
    position: absolute; right: 28px; top: 96px; width: 230px;
    color: var(--silver);
    font-size: 15px; letter-spacing: 1px; text-transform: uppercase; line-height: 1.3;
    padding-bottom: 6px; border-bottom: 1px solid var(--silver);
    display: flex; align-items: center; gap: 10px;
  }
  .brand-front__name { flex: 1; text-align: center; }
  .brand-front__dot { width: 12px; height: 12px; border-radius: 50%; background: var(--brand-blue); flex: none; }
  .tagline {
    position: absolute; right: 28px; top: 156px; width: 230px;
    color: var(--text-light); font-size: 10.5px; font-style: italic;
    line-height: 1.35; text-align: center;
  }

  .contact {
    position: absolute; left: 62px; bottom: 24px; list-style: none;
    color: var(--text-light); font-size: 13px; line-height: 1.5;
  }
  .contact__item { display: flex; align-items: center; gap: 8px; }
  .contact__icon { width: 11px; height: 11px; flex: none; }
  .contact__icon path, .contact__icon rect, .contact__icon circle { fill: var(--brand-blue); }
</style>
</head>
<body>
<main class="canvas">
  <section class="card card--back" aria-label="Card back">
    <div class="brand-mark"><span class="brand-mark__dot"></span>Harborview Nest Advisors, LLC</div>
    <p class="disclosure">Gregor Pelham is a registered representative of and offers securities through Brightmoor Capital Brokerage Corporation, Member FNQX. Brightmoor Capital Brokerage Corporation is a member of the Brightmoor Capital Alliance which is the marketing name for Brightmoor Holding Corporation and its affiliates.</p>
  </section>

  <section class="card card--front" aria-label="Card front">
    <div class="card__band"></div>

    <div class="person">
      <p class="person__name">Gregor Pelham</p>
      <p class="person__creds">MBA, ChFC®, CLU®</p>
      <p class="person__role">Financial Advisor,<br>Registered Representative</p>
    </div>

    <div class="brand-front"><span class="brand-front__dot"></span><span class="brand-front__name">Harborview Nest Advisors, LLC</span></div>
    <p class="tagline">Turning Your Earned Income<br>Into Retirement Income</p>

    <ul class="contact">
      <li class="contact__item">
        <svg class="contact__icon" viewBox="0 0 12 12"><path d="M2 1h2.5l1 3-1.5 1a6 6 0 0 0 3 3l1-1.5 3 1V10a1 1 0 0 1-1 1A9 9 0 0 1 1 2a1 1 0 0 1 1-1z"/></svg>
        (555) 318-2946
      </li>
      <li class="contact__item">
        <svg class="contact__icon" viewBox="0 0 12 12"><rect x="1" y="4" width="10" height="6" rx="1"/><rect x="3" y="1" width="6" height="3"/></svg>
        (800) 555-0193
      </li>
      <li class="contact__item">
        <svg class="contact__icon" viewBox="0 0 12 12"><circle cx="6" cy="6" r="5"/></svg>
        www.harborviewnest.example
      </li>
      <li class="contact__item">
        <svg class="contact__icon" viewBox="0 0 12 12"><rect x="1" y="2.5" width="10" height="7" rx="1"/></svg>
        gpelham@harborviewnest.example
      </li>
      <li class="contact__item">
        <svg class="contact__icon" viewBox="0 0 12 12"><path d="M6 0.5a4 4 0 0 1 4 4c0 3-4 7-4 7s-4-4-4-7a4 4 0 0 1 4-4z"/></svg>
        2187 Meadowlark Ridge Rd. Suite K418 Virginia Beach, VA 23999
      </li>
    </ul>
  </section>
</main>
</body>
</html>
```